Casino with the 'highest winning percentage' needs a stationery design

This is for a casino in Colombo, Sri Lanka and we need a stationery design for business card, letter head and envelope.

Should be very professional, simple and elegant without fancy fonts

Reason: Not fully satisfied with the designs. Need more designs.

Business

• 1. card deck symbol 'CLUBS' in red, or black

2. name in BLOCK CAPITAL LETTERS

3. Preferred font colours are black, white or red

4. Prefer 'professional /elegant' fonts
• SHOULD NOT HAVE ANY OTHER SYMBOL EXCEPT 'CLUBS'

DO NOT PREFER ITALIC FONTS

```html
<!DOCTYPE html>
<html lang="en">
<head>
<meta charset="utf-8">
<title>Marlowe Casino — Stationery</title>
<link rel="stylesheet" href="https://fonts.googleapis.com/css2?family=Marcellus&family=Questrial&family=Tinos:wght@400;700&display=swap">
<style>
  :root {
    --backdrop: #a9aab3;
    --folder: #2b2c30;
    --folder-inner: #232428;
    --pattern: #3a3b40;
    --gold: #c9975a;
    --paper: #ffffff;
    --paper-shade: #f2f3f6;
    --ink: #1d1d1f;
    --ink-soft: #55565a;
  }
  * { box-sizing: border-box; margin: 0; padding: 0; }
  html, body { width: 1200px; height: 968px; overflow: hidden; }
  body { background: var(--backdrop); position: relative; font-family: "Questrial", sans-serif; }

  .folder-open { position: absolute; left: 140px; top: 300px; width: 832px; height: 578px; background: var(--folder-inner); }
  .folder-open__pattern { position: absolute; left: 334px; top: 0; width: 80px; height: 578px; background: var(--pattern); }
  .folder-open__pattern--right { left: 790px; width: 42px; height: 380px; }
  .folder-open__spine { position: absolute; left: 414px; top: 0; width: 2px; height: 578px; background: #18191c; }
  .folder-open__sheet { position: absolute; left: 432px; top: 10px; width: 386px; height: 368px; background: var(--paper-shade); }
  .folder-open__pocket { position: absolute; left: 416px; top: 378px; width: 416px; height: 200px; background: var(--folder); }
  .folder-open__slot { position: absolute; left: 724px; top: 376px; width: 32px; height: 32px; border-radius: 50%; background: #1b1c1f; }
  .pocket-contact { position: absolute; right: 42px; top: 110px; text-align: center; color: var(--gold); font-size: 6px; line-height: 8px; }
  .pocket-contact__rule { width: 80px; height: 1px; background: var(--gold); margin: 5px auto 4px; }
  .pocket-contact__web { font-size: 7px; }

  .folder-cover { position: absolute; left: 92px; top: 240px; width: 386px; height: 560px; background: var(--folder); box-shadow: 4px 4px 12px rgba(0,0,0,.25); text-align: center; }
  .brand { font-family: "Marcellus", serif; color: var(--gold); letter-spacing: 1px; }
  .folder-cover .brand__mark { width: 14px; height: 14px; border-radius: 50%; background: var(--gold); margin: 168px auto 26px; }
  .folder-cover .brand__name { font-size: 27px; line-height: 30px; }
  .folder-cover .tagline { color: var(--gold); font-size: 10.5px; line-height: 12px; margin-top: 8px; }

  .letterhead { position: absolute; left: 681px; top: 67px; width: 386px; height: 558px; background: var(--paper); box-shadow: 2px 3px 8px rgba(0,0,0,.18); font-family: "Tinos", serif; color: var(--ink); font-size: 6px; line-height: 9px; }
  .letterhead__brand { position: absolute; left: 161px; top: 32px; width: 80px; text-align: center; color: var(--ink); letter-spacing: 0; }
  .letterhead__brand .brand__mark { width: 8px; height: 8px; border-radius: 50%; background: var(--ink); margin: 0 auto 28px; }
  .letterhead__brand .brand__name { color: var(--ink); font-size: 11px; line-height: 12px; }
  .letterhead__brand .tagline { font-family: "Questrial", sans-serif; font-size: 5px; line-height: 6px; margin-top: 3px; }
  .letter__recipient { position: absolute; left: 66px; top: 112px; }
  .letter__subject { position: absolute; left: 66px; top: 176px; font-weight: 700; }
  .letter__date { position: absolute; right: 70px; top: 176px; }
  .letter__body { position: absolute; left: 66px; top: 222px; width: 252px; text-align: justify; }
  .letter__body p { margin-bottom: 9px; }
  .letter__signature { position: absolute; left: 62px; top: 404px; width: 92px; height: 48px; background: linear-gradient(90deg, #ececef, #f7f7f9); }
  .letter__signer { position: absolute; left: 66px; top: 454px; }
  .letter__footer { position: absolute; left: 140px; top: 502px; width: 120px; text-align: center; font-family: "Questrial", sans-serif; font-size: 4px; line-height: 5px; }
  .letter__footer-rule { width: 64px; height: 1px; background: var(--ink-soft); margin: 4px auto 2px; }

  .business-card { position: absolute; left: 686px; top: 67px; width: 170px; height: 90px; background: var(--paper); box-shadow: 1px 2px 5px rgba(0,0,0,.2); font-size: 4.5px; line-height: 5.5px; color: var(--ink); }
  .business-card .brand { position: absolute; left: 20px; top: 10px; display: flex; align-items: center; gap: 4px; color: var(--ink-soft); }
  .business-card .brand__mark { width: 6px; height: 6px; border-radius: 50%; background: var(--ink-soft); }
  .business-card .brand__name { font-size: 10px; line-height: 11px; }
  .business-card__person { position: absolute; left: 108px; top: 50px; }
  .business-card__person strong { font-size: 5px; letter-spacing: .3px; }
  .business-card__address { position: absolute; left: 38px; top: 63px; text-align: right; width: 64px; }
  .business-card__contact { position: absolute; left: 108px; top: 63px; }

  .card-back { position: absolute; left: 1007px; top: 705px; width: 64px; height: 167px; background: var(--folder); padding: 5px; }
  .card-back__pattern { width: 100%; height: 100%; background: var(--pattern); }
</style>
</head>
<body>

  <section class="folder-open" aria-label="Presentation folder, open">
    <div class="folder-open__pattern" role="img" aria-label="Repeating outline club pattern on the inner flap"></div>
    <div class="folder-open__spine"></div>
    <div class="folder-open__sheet"></div>
    <div class="folder-open__pattern folder-open__pattern--right" role="img" aria-label="Repeating outline club pattern on the inner panel"></div>
    <div class="folder-open__pocket">
      <div class="pocket-contact">
        <div>MARLOWE LIMITED</div>
        <div>12, Harbour Lane</div>
        <div>Colombo 01000, Sri Lanka</div>
        <div>Tel: +94 11 5550123</div>
        <div>Fax: +94 11 5550124</div>
        <div class="pocket-contact__rule"></div>
        <div class="pocket-contact__web">www.marlowecolombo.com</div>
      </div>
    </div>
    <div class="folder-open__slot"></div>
  </section>

  <section class="folder-cover" aria-label="Presentation folder cover">
    <div class="brand">
      <div class="brand__mark"></div>
      <div class="brand__name">MARLOWE<br>CASINO</div>
    </div>
    <p class="tagline">Where Every Game<br>Is Played Fair</p>
  </section>

  <article class="letterhead" aria-label="Letterhead">
    <div class="letterhead__brand brand">
      <div class="brand__mark"></div>
      <div class="brand__name">MARLOWE<br>CASINO</div>
      <p class="tagline">Where Every Game<br>Is Played Fair</p>
    </div>
    <div class="letter__recipient">Colorios 96<br>3550 Birtieullort</div>
    <div class="letter__subject">Demper sed feugiat felis hendrerit<br>ACCD Aenean scelerisque lorem aliquam.</div>
    <div class="letter__date">18.13.2013<br>Froundenberg</div>
    <div class="letter__body">
      <p>Vitae gravida,</p>
      <p>Lorem ipsum dolor sit amet, consectetur adipiscing elit. Aenean aliquet, dui sodales blandit accumsan, lorem arcu volutpat orci, nec ultrices nulla neque id turpis. Integer non vulputate magna. Fusce nisl leo, pharetra non fringilla a, ornare a erat.</p>
      <p>Pellentesque gravida porttitor dolor vel congue. Morbi rhoncus purus eget nulla egestas laoreet. Morbi vehicula venenatis consectetur. Phasellus aliquam tellus sed elit consequat sodales. Cras et mauris metus. Lorem ipsum dolor sit amet, consectetur adipiscing elit. Fusce porta dui sed leo posuere aliquet.</p>
      <p>Donec sed odio sit amet nisi dapibus consectetur ut sed lorem. In porttitor, nisi eu egestas fringilla, purus nulla adipiscing nulla, eget sagittis nisi augue nec odio. Ut convallis malesuada mauris eu pellentesque. Donec faucibus pellentesque volutpat.</p>
      <p>Etiam placerat, nulla vel tincidunt mattis, tortor augue accumsan turpis, vitae gravida ipsum arcu vitae lorem. Aliquam vel neque commodo blandit. Nullam sit quam lacus. Donec in ante ac lorem bibendum. Aenean egestas semper tincidunt. Curabitur mollis nunc non lorem imperdiet elementum. Integer porttitor vulputate feugiat. Vivamus commodo diam non.</p>
    </div>
    <div class="letter__signature" role="img" aria-label="Handwritten signature"></div>
    <div class="letter__signer">Owen Castell<br>Managium Directus</div>
    <div class="letter__footer">
      <div>MARLOWE LIMITED</div>
      <div>12, Harbour Lane</div>
      <div>Colombo 01000, Sri Lanka</div>
      <div>Tel: +94 11 5550123</div>
      <div>Fax: +94 11 5550124</div>
      <div class="letter__footer-rule"></div>
      <div>www.marlowecolombo.com</div>
    </div>
  </article>

  <article class="business-card" aria-label="Business card, front">
    <div class="brand">
      <div class="brand__mark"></div>
      <div class="brand__name">MARLOWE<br>CASINO</div>
    </div>
    <div class="business-card__person"><strong>DANIEL REEVE</strong><br>Manager</div>
    <div class="business-card__address">MARLOWE LIMITED<br>12, Harbour Lane<br>Colombo 01000, Sri Lanka</div>
    <div class="business-card__contact">Tel: +94 11 5550123<br>Fax: +94 11 5550124<br>www.marlowecolombo.com</div>
  </article>

  <article class="card-back" aria-label="Business card, back">
    <div class="card-back__pattern" role="img" aria-label="Repeating outline club pattern"></div>
  </article>

</body>
</html>
```